Business Card - high end, modern health care

Hey designers!

We need a double sided business card for the boutique, cutting edge physical therapy rehabilitation centre in Sydney's Northern Beaches.

With the most qualified physios in the area The Harbourview Motion Clinic does what other physiotherapy practices do not, we take our time with our patients giving them longer appointments, better physios and therefor faster results!

We guarantee that the service people receive at THMC will be unparalleled.

Hence we need a business card to reflect our modern, boutique, high end service. The final design needs to reflect that we are in a class of our own yet with the feel of beachside retreat.

Below I have attached our logo in both blue on white and white on blue. The exact colour is;
and the font that we have used in our logo is Tex Gyre Aventador.

I like the idea of the blue as the main colour as it is more eye catching and our signage onto the main road will be in this blue and in the interest of consistency across marketing the blue needs to be a part of the design. However I would appreciate a few designs onto a wooden background as this is a visual theme within the fitout of the practice.

The design needs to be of standard size (91x55mm).

Target Market(s)

We target people who have an end outcome in mind and those who have had poor experiences with other providers and ensure that everyone gets the care that they deserve with a premium service that is tailored to the individuals circumstances. As a premium service, the target market is highly educated, business and tech savvy with the additional target market of elderly people who have self funded their retirement and see value in paying for the best ongoing rehabilitation to maintain independence.

Industry/Entity Type

Physical Therapy

Contact Information for Business Card

Name, designation( Titled Musculoskeletal Physiotherapist... there will also be those in the company that have multiple designations ie 5 or 6 words long), phone number, email, facebook, instagram, address

Font styles to use
Sans Serif

Colors

Designer to choose colors to be used in the design.

Requirements
Must have
• Front - The logo as large as possible, blue or wooden theme, and all of the important details.
• Back - A blank space/lines on which to write appointment times (no "Appointment, date, time" etc.)
Nice to have
• facebook url
• logos for facebook and instagram
• Mini logos for the phone and email?

```html
<!DOCTYPE html>
<html lang="en">
<head>
<meta charset="utf-8">
<title>The Harbourview Motion Clinic – Business Card</title>
<link href="https://fonts.googleapis.com/css2?family=Lato:wght@400;700;900&display=swap" rel="stylesheet">
<style>
  :root {
    --stage: #1c1c1e;
    --brand-blue: #0555a8;
    --card-black: #161616;
    --card-white: #ffffff;
    --card-grey: #ececec;
    --ink: #1a1a1a;
    --text-light: #ffffff;
  }
  * { box-sizing: border-box; margin: 0; padding: 0; }
  html, body {
    width: 1200px; height: 900px; overflow: hidden;
    background: var(--stage);
    font-family: "Lato", sans-serif;
  }
  .canvas {
    position: relative; width: 1200px; height: 900px;
    display: flex; align-items: center; justify-content: center; gap: 40px;
  }
  .card {
    position: relative; width: 520px; height: 314px;
    border-radius: 22px; overflow: hidden;
    box-shadow: 0 18px 40px rgba(0,0,0,.55);
  }

  /* Back side */
  .card-back { background: var(--card-black); }
  .back-brand {
    position: absolute; left: 0; right: 0; top: 0; height: 218px;
    display: flex; align-items: center; justify-content: center; gap: 14px;
  }
  .brand-dot {
    width: 34px; height: 34px; border-radius: 50%;
    background: var(--brand-blue); flex: none;
  }
  .back-brand .brand-name {
    color: var(--brand-blue); font-weight: 900; font-size: 20px;
    letter-spacing: .04em; text-transform: uppercase;
  }
  .appointment-band {
    position: absolute; left: 0; right: 0; bottom: 0; height: 96px;
    background: var(--card-white);
    display: flex; align-items: flex-end; justify-content: center;
    padding-bottom: 34px; gap: 6px;
    font-size: 12px; font-weight: 700; color: var(--ink);
  }
  .write-line {
    display: inline-block; height: 1px; background: var(--ink);
    margin-bottom: 3px;
  }
  .write-line.date { width: 160px; }
  .write-line.time { width: 200px; }

  /* Front side */
  .card-front { background: var(--brand-blue); }
  .front-top {
    position: absolute; left: 0; right: 0; top: 0; height: 172px;
    background: var(--card-grey);
    display: flex; align-items: center; justify-content: center;
  }
  .front-logo { display: flex; align-items: center; gap: 12px; }
  .front-logo .brand-dot { width: 50px; height: 50px; }
  .front-logo .brand-name {
    color: var(--brand-blue); font-weight: 900; text-transform: uppercase;
    line-height: 1.05;
  }
  .brand-name .line-main { display: block; font-size: 26px; letter-spacing: .01em; }
  .brand-name .line-sub { display: block; font-size: 17px; letter-spacing: .2em; }

  .front-details {
    position: absolute; left: 0; right: 0; top: 172px; bottom: 0;
    color: var(--text-light);
    display: flex; justify-content: space-between;
    padding: 22px 28px 20px 30px;
  }
  .person-name { font-size: 18px; font-weight: 900; letter-spacing: .02em; text-transform: uppercase; }
  .person-role { font-size: 13px; margin-top: 2px; }
  .social-list { list-style: none; margin-top: 18px; font-size: 13px; }
  .social-list li, .contact-list li { display: flex; align-items: center; gap: 6px; margin-top: 4px; }
  .social-mark {
    width: 14px; height: 14px; border-radius: 50%;
    background: var(--text-light); flex: none;
  }
  .contact-list { list-style: none; font-size: 13px; padding-top: 2px; }
  .contact-list svg { width: 14px; height: 14px; flex: none; }
</style>
</head>
<body>
<main class="canvas">

  <section class="card card-back" aria-label="Card back">
    <div class="back-brand">
      <span class="brand-dot"></span>
      <span class="brand-name">The Harbourview Motion Clinic</span>
    </div>
    <div class="appointment-band">
      <span>DATE</span><span class="write-line date"></span>
      <span>TIME</span><span class="write-line time"></span>
    </div>
  </section>

  <section class="card card-front" aria-label="Card front">
    <div class="front-top">
      <div class="front-logo">
        <span class="brand-dot"></span>
        <span class="brand-name">
          <span class="line-main">The Harbourview</span>
          <span class="line-sub">Motion Clinic</span>
        </span>
      </div>
    </div>
    <div class="front-details">
      <div class="person">
        <p class="person-name">Daniel Reeves</p>
        <p class="person-role">Managing Director</p>
        <ul class="social-list">
          <li><span class="social-mark"></span>/harbourviewmotionclinic</li>
          <li><span class="social-mark"></span>@harbourviewmotionclinic</li>
        </ul>
      </div>
      <ul class="contact-list">
        <li>
          <svg viewBox="0 0 16 16" aria-hidden="true"><circle cx="8" cy="8" r="7.2" fill="none" stroke="#fff" stroke-width="1.2"/><path d="M5.3 4.3l1.3-.3.8 1.9-.9.7c.4.9 1.1 1.6 2 2l.7-.9 1.9.8-.3 1.3c-3 .3-5.8-2.5-5.5-5.5z" fill="#fff"/></svg>
          444 555 0192
        </li>
        <li>
          <svg viewBox="0 0 16 16" aria-hidden="true"><circle cx="8" cy="8" r="7.2" fill="none" stroke="#fff" stroke-width="1.2"/><rect x="4.2" y="5.2" width="7.6" height="5.6" fill="#fff"/><path d="M4.2 5.4L8 8.3l3.8-2.9" fill="none" stroke="#0555a8" stroke-width="0.9"/></svg>
          hello@harbourviewmotion.com
        </li>
      </ul>
    </div>
  </section>

</main>
</body>
</html>
```